Brell Stone Company Business Cards

Front and Back Business Card - logo and text setup - cool design. I need workable photoshop or illustrator files so I can setup each employee card with design that is created
Updates

Hi everyone, thank you for the great entries. Please no more white and blue cards - there are so many already - black and silver only now please. thanks!

Target Market(s)

Construction Industry - Facility Managers

Industry/Entity Type

Construction

Contact Information for Business Card

I really like contemporary simplistic looks - clean neat....not opposed to seeing some black backrounds

Requirements
Must have
• Logo/website address with design on front only - www.brellstone-example.com (logo attached)
• Back:
• Name/Title/Company Address/Phone/email address
Nice to have
• Cool design
Should not have
• Nothing gimmicky like Fire or Water - since we are a Fire Protection company - it has all been done

```html
<!DOCTYPE html>
<html lang="en">
<head>
<meta charset="utf-8">
<title>Brell Stone Company – Business Cards</title>
<link rel="stylesheet" href="https://fonts.googleapis.com/css2?family=Jost:wght@400;600&family=Open+Sans:wght@400;800&display=swap">
<style>
  :root {
    --backdrop: #c8cdd2;
    --card-dark: #1c1c1c;
    --card-mid: #343434;
    --brand-red: #ee2a30;
    --brand-blue: #273a93;
    --white: #ffffff;
  }
  * { margin: 0; padding: 0; box-sizing: border-box; }
  html, body { width: 1200px; height: 1193px; overflow: hidden; }
  body { background: var(--backdrop); position: relative; font-family: "Open Sans", sans-serif; color: var(--white); }

  .card {
    position: absolute; width: 873px; height: 499px; border-radius: 38px; overflow: hidden;
    background: radial-gradient(ellipse at 50% 0%, var(--card-mid) 0%, var(--card-dark) 55%, #0b0b0b 100%);
  }
  .card--contact { left: 77px; top: 73px; }
  .card--brand { left: 255px; top: 613px; }

  .wordmark { position: absolute; display: flex; align-items: center; gap: 18px; transform: translateX(-50%); white-space: nowrap; }
  .wordmark__square { background: var(--brand-red); }
  .wordmark__name { font-family: "Open Sans", sans-serif; font-weight: 800; color: var(--brand-blue); letter-spacing: -1px; }
  .card--contact .wordmark { left: 421px; top: 78px; }
  .card--contact .wordmark__square { width: 40px; height: 40px; }
  .card--contact .wordmark__name { font-size: 72px; }
  .card--brand .wordmark { left: 436px; top: 175px; }
  .card--brand .wordmark__square { width: 52px; height: 52px; }
  .card--brand .wordmark__name { font-size: 94px; }

  .band-blue { position: absolute; left: 0; top: 305px; width: 100%; height: 194px; background: var(--brand-blue); }
  .band-red-right { position: absolute; left: 440px; top: 255px; right: 0; height: 50px; background: var(--brand-red); }
  .band-red-left { position: absolute; left: 0; top: 255px; width: 490px; height: 106px; background: var(--brand-red); border-bottom: 3px solid var(--white); }
  .avatar { position: absolute; left: 384px; top: 241px; }

  .person { position: absolute; left: 32px; width: 320px; top: 272px; text-align: center; font-family: "Jost", sans-serif; white-space: nowrap; }
  .person__name { font-size: 30px; font-weight: 600; letter-spacing: 0.5px; line-height: 1.15; }
  .person__title { font-size: 29px; font-weight: 400; letter-spacing: 1px; line-height: 1.2; }

  .address { position: absolute; left: 53px; top: 401px; font-size: 21px; line-height: 36px; white-space: nowrap; }
  .address__line { display: flex; align-items: center; gap: 7px; }
  .address__line--indent { padding-left: 25px; }

  .contact-list { position: absolute; left: 502px; top: 360px; list-style: none; font-size: 21px; white-space: nowrap; }
  .contact-list li { display: flex; align-items: center; gap: 10px; height: 41px; }
  .contact-list svg { flex: none; }

  .site-url { position: absolute; left: 0; width: 100%; top: 438px; text-align: center; font-size: 27px; letter-spacing: 5px; }
</style>
</head>
<body>

<section class="card card--contact" aria-label="Business card front">
  <div class="wordmark"><span class="wordmark__square"></span><span class="wordmark__name">Brell Stone</span></div>

  <div class="band-blue"></div>
  <div class="band-red-right"></div>
  <div class="band-red-left"></div>
  <svg class="avatar" width="124" height="124" viewBox="0 0 124 124" aria-hidden="true">
    <circle cx="62" cy="62" r="59" fill="#ee2a30" stroke="#fff" stroke-width="4"/>
    <circle cx="62" cy="42" r="17" fill="#fff"/>
    <path d="M31 93 C31 71 45 62 62 62 C79 62 93 71 93 93 Z" fill="#fff"/>
  </svg>

  <div class="person">
    <div class="person__name">DARREN HOLCOMB</div>
    <div class="person__title">PRESIDENT</div>
  </div>

  <div class="address">
    <div class="address__line">
      <svg width="18" height="20" viewBox="0 0 18 20" aria-hidden="true"><circle cx="9" cy="10" r="8" fill="none" stroke="#fff" stroke-width="1.6"/><path d="M9 15 C6 11 6 9 6 8 a3 3 0 0 1 6 0 c0 1 0 3 -3 7z" fill="#fff"/></svg>
      <span>48 Meridian Park Way</span>
    </div>
    <div class="address__line address__line--indent">Harlow Bay, NY 10990</div>
  </div>

  <ul class="contact-list">
    <li>
      <svg width="24" height="22" viewBox="0 0 26 24" aria-hidden="true"><path d="M5 2 L9 2 L11 8 L8 10 C10 14 12 16 16 18 L18 15 L24 17 L24 21 C24 22 23 23 21 23 C11 22 3 14 2 5 C2 3 3 2 5 2Z" fill="#fff"/></svg>
      <span>(555) 214-0392</span>
    </li>
    <li>
      <svg width="24" height="19" viewBox="0 0 26 20" aria-hidden="true"><rect x="1" y="2" width="24" height="16" fill="#fff"/><path d="M1 2 L13 11 L25 2 M1 18 L10 9 M25 18 L16 9" stroke="#273a93" stroke-width="1.6" fill="none"/></svg>
      <span>info@brellstone-example.com</span>
    </li>
    <li>
      <svg width="24" height="24" viewBox="0 0 26 26" aria-hidden="true"><g fill="none" stroke="#fff" stroke-width="1.6"><circle cx="13" cy="13" r="11"/><ellipse cx="13" cy="13" rx="5" ry="11"/><path d="M2 13 H24 M4 7 H22 M4 19 H22"/></g></svg>
      <span>www.brellstone-example.com</span>
    </li>
  </ul>
</section>

<section class="card card--brand" aria-label="Business card back">
  <div class="wordmark"><span class="wordmark__square"></span><span class="wordmark__name">Brell Stone</span></div>
  <div class="site-url">www.brellstone-example.com</div>
</section>

</body>
</html>
```